Ridge Lass Crew (Flyer)

I want a flyer to advertise my service.
Details below, and logo's to use are attached.

A girls only after school program, 11-14yrs, as OSHC is no longer avail, dedicated to coaching & mentoring our girls into strong, independent young women.

The Brainchild of Rebecca Folwin, Ridge Lass Crew was created to address the growing demand for after school/school holiday supervision for kids moving from primary into high school, when OSHC ceases to exist.
With over 12 years experience mentoring and coaching young women in the corporate world, Bec decided to leave her role as a Director with Tarrant Trust, and follow her passion.
Bec, along with her sister Lorraine, who has over 10 years experience in local communities as a Youth Worker, and is also a qualified Enrolled Nurse, embarked on building a program designed to keep parents happy (by knowing their girls are safe) and dedicated to coaching and mentoring our girls into strong, independent young women.
Open every afternoon and during school holidays, we look to offer;
- Daily meditation
- Healthy snacks
- Dedicated homework time
- Organised group activity, led by qualified instructors (yoga, fitness class, soccer etc)
- Regular guests speakers, addressing issues/concerns for young people today
- SOCIAL MEDIA FREE ZONE

Located 87 Pelham Pde, Baulkham Hills (across from Crestmoor Day Clinic)
Open 3-6pm Monday to Friday

Facebook page: http://fb.example/ridgelasscrew
Email: info@ridgelasscrew.example.au
Mobile: 0455817396

Target Market(s)

Parents of teenage girls, teenage girls 11-14 years

Industry/Entity Type

School

Font styles to use
Sans Serif

Colors
b768aa
e667a6

Requirements
Must have
• What progam is - see brief
• Who runs it
Should not have
• Not be too busy, not overly mature images

```html
<!DOCTYPE html>
<html lang="en">
<head>
<meta charset="utf-8">
<title>Ridge Lass Crew – After School Program Flyer</title>
<link rel="stylesheet" href="https://fonts.googleapis.com/css2?family=Cinzel:wght@400;700&family=Open+Sans:wght@400;600;700&family=Roboto+Condensed:wght@300;400;700&family=Carlito&family=Pinyon+Script&display=swap">
<style>
  :root {
    --pink: #e667a6;
    --pink-light: #f08cc0;
    --purple: #b768aa;
    --ink: #111111;
    --slate: #3a3f4a;
    --white: #ffffff;
    --mist: #eeecef;
  }
  * { margin: 0; padding: 0; box-sizing: border-box; }
  html, body { width: 848px; height: 1200px; overflow: hidden; background: var(--white); }
  .flyer { position: relative; width: 848px; height: 1200px; overflow: hidden; font-family: "Open Sans", sans-serif; color: var(--ink); }
  .backdrop { position: absolute; inset: 0; width: 848px; height: 1200px; }
  .abs { position: absolute; white-space: nowrap; }

  .brand-box { left: 606px; top: 4px; width: 220px; height: 294px; background: var(--white); display: flex; flex-direction: column; align-items: center; justify-content: center; }
  .brand-name { font-family: "Open Sans", sans-serif; font-weight: 700; font-size: 34px; line-height: 1.15; color: var(--pink); text-align: center; }

  .headline { font-family: "Cinzel", serif; font-weight: 700; color: var(--ink); }
  .headline--girls { left: 544px; top: 324px; font-size: 39px; }
  .headline--program { left: 472px; top: 386px; font-size: 27.5px; letter-spacing: 0.3px; }
  .headline--ages { left: 436px; top: 454px; font-size: 35px; }
  .ages-note { left: 530px; top: 504px; font-size: 19px; font-weight: 600; letter-spacing: 0.3px; }

  .section-title--about { left: 66px; top: 598px; font-family: "Roboto Condensed", sans-serif; font-size: 28px; }
  .about-text { position: absolute; left: 27px; top: 663px; width: 400px; font-family: "Carlito", sans-serif; font-size: 21px; line-height: 28.6px; }

  .section-title--offer { left: 545px; top: 596px; font-size: 24px; font-weight: 700; color: var(--slate); letter-spacing: 0.5px; }
  .offer-item { font-size: 19.5px; color: var(--ink); }
  .offer-item::before { content: ""; position: absolute; left: -30px; top: 9px; width: 9px; height: 9px; border-radius: 50%; background: var(--pink); }
  .offer-item--sub { font-size: 19.5px; }

  .signoff { left: 0; width: 848px; text-align: center; }
  .signoff--founder { top: 942px; font-family: "Cinzel", serif; font-weight: 700; font-size: 23px; }
  .signoff--name { top: 978px; font-family: "Cinzel", serif; font-size: 36px; letter-spacing: 2px; }
  .signoff--tagline { font-family: "Pinyon Script", cursive; font-size: 19px; }
  .signoff--line1 { top: 1045px; }
  .signoff--line2 { top: 1082px; }

  .contact { font-family: "Roboto Condensed", sans-serif; color: var(--ink); }
  .contact--label { left: 158px; top: 1126px; font-size: 17px; display: flex; align-items: center; gap: 6px; }
  .contact--email { left: 16px; top: 1150px; font-size: 16.5px; }
  .contact--social { left: 16px; top: 1174px; font-size: 16.5px; display: flex; align-items: center; gap: 6px; }
  .social-dot { width: 16px; height: 16px; border-radius: 50%; background: var(--ink); display: inline-block; }
  .contact--phone { left: 310px; top: 1150px; font-size: 24px; font-weight: 300; letter-spacing: 0.5px; }
  .contact--address { left: 578px; top: 1152px; font-size: 19px; font-weight: 700; color: var(--white); display: flex; align-items: center; gap: 4px; letter-spacing: -0.3px; }
</style>
</head>
<body>
<div class="flyer">
  <svg class="backdrop" viewBox="0 0 1060 1500" width="848" height="1200">
    <defs>
      <linearGradient id="body-fade" x1="0" y1="0" x2="0" y2="1">
        <stop offset="0" stop-color="#ffffff"/>
        <stop offset="1" stop-color="#ecebee"/>
      </linearGradient>
      <linearGradient id="wave-fade" x1="0" y1="0" x2="1" y2="0">
        <stop offset="0" stop-color="#f08cc0"/>
        <stop offset="0.6" stop-color="#e667a6"/>
        <stop offset="1" stop-color="#c472b2"/>
      </linearGradient>
      <radialGradient id="photo-tone" cx="0.45" cy="0.45" r="0.65">
        <stop offset="0" stop-color="#e6e3e4"/>
        <stop offset="0.6" stop-color="#cfc6c4"/>
        <stop offset="1" stop-color="#b8aca6"/>
      </radialGradient>
    </defs>
    <rect width="1060" height="1500" fill="url(#body-fade)"/>
    <rect x="0" y="0" width="1060" height="548" fill="#e667a6"/>
    <path d="M560 548 L1060 548 L1060 680 L425 680 Q500 620 560 548 Z" fill="#b768aa"/>
    <circle cx="230" cy="260" r="466" fill="#ffffff"/>
    <circle cx="230" cy="260" r="460" fill="url(#photo-tone)" role="img" aria-label="Photo of a girl wearing a white program t-shirt"/>
    <path d="M0 1360 Q560 1420 1060 1300 L1060 1500 L0 1500 Z" fill="url(#wave-fade)"/>
    <path d="M0 1410 Q230 1395 340 1500 L0 1500 Z" fill="#ffffff"/>
    <path d="M680 1500 Q820 1415 1060 1385 L1060 1500 Z" fill="#b768aa"/>
  </svg>

  <div class="abs brand-box"><div class="brand-name">Ridge<br>Lass<br>Crew</div></div>

  <div class="abs headline headline--girls">A Girls Only</div>
  <div class="abs headline headline--program">After School Program</div>
  <div class="abs headline headline--ages">For 11-14yrs</div>
  <div class="abs ages-note">as OSHC is no longer available</div>

  <div class="abs section-title--about">ABOUT US</div>
  <p class="about-text">The Brainchild of Rebecca Folwin, Ridge Lass Crew was created to address the growing demand for after school/school holiday supervision for kids moving from primary into high school, when OSHC ceases to exist.</p>

  <div class="abs section-title--offer">WHAT WE OFFER</div>
  <div class="abs offer-item" style="left:546px;top:645px">Daily meditation</div>
  <div class="abs offer-item" style="left:546px;top:685px">Healthy snacks</div>
  <div class="abs offer-item" style="left:544px;top:731px">Organised group activity,</div>
  <div class="abs offer-item--sub" style="left:552px;top:760px">(yoga, fitness class, soccer etc.)</div>
  <div class="abs offer-item" style="left:544px;top:784px">Regular guests speakers</div>
  <div class="abs offer-item" style="left:545px;top:833px">Dedicated homework time</div>
  <div class="abs offer-item" style="left:544px;top:880px">Social media free zone</div>

  <div class="abs signoff signoff--founder">The Brainchild of Rebecca Folwin</div>
  <div class="abs signoff signoff--name">Ridge Lass Crew</div>
  <div class="abs signoff signoff--tagline signoff--line1">Dedicated to Coaching &amp; Mentoring Our Girls</div>
  <div class="abs signoff signoff--tagline signoff--line2">into Strong, Independent Young women</div>

  <div class="abs contact contact--label">e-Mail us
    <svg width="18" height="14" viewBox="0 0 18 14" aria-hidden="true"><rect x="1" y="1" width="16" height="12" fill="none" stroke="#111" stroke-width="1.2"/><path d="M1 1 L9 8 L17 1" fill="none" stroke="#111" stroke-width="1.2"/></svg>
  </div>
  <div class="abs contact contact--email">info@ridgelasscrew.example.au</div>
  <div class="abs contact contact--social">http://fb.example/ridgelasscrew <span class="social-dot"></span></div>
  <div class="abs contact contact--phone">CALL US: 0455817396</div>
  <div class="abs contact contact--address">
    <svg width="22" height="30" viewBox="0 0 22 30" aria-hidden="true"><path d="M11 1 C5 1 1 5.5 1 11 C1 18 11 29 11 29 C11 29 21 18 21 11 C21 5.5 17 1 11 1 Z" fill="#ffffff"/><circle cx="11" cy="11" r="4" fill="#b768aa"/></svg>
    87 Pelham Pde, Baulkham Hills
  </div>
</div>
</body>
</html>
```